Beautiful design for wordpress

I need a beautiful, colourful and feminine website. My business is called 'The Velvet Lantern', and I sell crystals, books, CD's, pendulums and other metaphysical items. I also provide Reiki (energy healing).
I want this design to be eye catching and inspire happiness and joy in those who see it. And I would love to see the use of the logo and its colours :)
Please add these on the web design: Home, About, Online store, Blog

Industry/Entity Type

Business

Requirements
Must have
• Colourful and playful, must use the logo somewhere, have the words on a menu saying 'Home, Blog, Online store and about' (or similar to those)And the design must stand out!
Should not have
• grey, brown and other boring colours.

```html
<!DOCTYPE html>
<html lang="en">
<head>
<meta charset="utf-8">
<title>The Velvet Lantern</title>
<link href="https://fonts.googleapis.com/css2?family=Open+Sans:wght@400;600;700&display=swap" rel="stylesheet">
<style>
  :root{
    --pink:#e8318a;
    --pink-dark:#c81f73;
    --pink-soft:#f25aa5;
    --ink:#333333;
    --muted:#777777;
    --line:#e4e4e4;
    --tile-bar:#f1f1f1;
    --footer:#1e1e1e;
    --footer-deep:#141414;
    --white:#ffffff;
  }
  *{margin:0;padding:0;box-sizing:border-box}
  html,body{width:851px;height:1200px;overflow:hidden;background:var(--white)}
  body{font-family:"Open Sans",Arial,sans-serif;color:var(--ink);position:relative}

  /* header */
  .site-header{position:absolute;left:0;top:0;width:851px;height:113px}
  .brand{position:absolute;left:50px;top:26px;display:flex;align-items:center;gap:10px}
  .brand-dot{width:26px;height:26px;border-radius:50%;background:var(--pink)}
  .brand-name{font-size:19px;font-weight:700;color:var(--pink);line-height:1.1;width:110px}
  .search{position:absolute;left:530px;top:30px;width:193px;height:24px;border:1px solid var(--line);
    font-size:10px;color:#999;padding:5px 8px}
  .search svg{position:absolute;right:6px;top:6px}
  .main-nav{position:absolute;left:525px;top:74px;width:198px;height:24px;background:var(--pink);
    display:flex;align-items:center;justify-content:space-around;padding:0 4px}
  .main-nav a{color:var(--white);font-size:8.5px;text-decoration:none;padding:3px 5px}
  .main-nav a.active{background:var(--pink-dark)}

  /* hero */
  .hero{position:absolute;left:0;top:113px;width:851px;height:392px;
    background:radial-gradient(circle at 72% 55%,#d3212b 0 16%,rgba(211,33,43,0) 30%),
      radial-gradient(circle at 15% 75%,#e6cf9c 0 12%,rgba(230,207,156,0) 26%),
      radial-gradient(circle at 85% 20%,#fff6e2 0 10%,rgba(255,246,226,0) 30%),
      linear-gradient(160deg,#f4ead6 0%,#e9d3a8 45%,#c9a36a 100%)}
  .hero-caption{position:absolute;left:100px;top:326px;width:356px;height:58px;background:rgba(0,0,0,.6);
    color:var(--white);font-size:11.5px;font-weight:600;line-height:1.5;padding:10px 14px}
  .slider-dots{position:absolute;left:400px;top:478px;display:flex;gap:5px}
  .slider-dots span{width:8px;height:8px;border-radius:50%;background:rgba(0,0,0,.55)}
  .slider-dots span.on{background:var(--white)}

  /* welcome */
  .welcome{position:absolute;left:128px;top:524px;width:596px;text-align:center}
  .section-title{font-size:13px;font-weight:600;color:var(--ink)}
  .welcome p{margin-top:12px;font-size:7.5px;line-height:1.65;color:var(--muted)}
  .rule{position:absolute;left:128px;width:596px;height:1px;background:var(--line)}

  /* products */
  .products-title{position:absolute;left:128px;top:638px;width:596px;text-align:center}
  .product{position:absolute;top:675px;width:142px}
  .product-img{height:98px}
  .product-bar{margin-top:8px;height:22px;background:var(--tile-bar);display:flex;align-items:center;
    justify-content:space-between;padding:0 8px;font-size:9px;color:var(--ink)}
  .product-bar i{width:12px;height:12px;border-radius:50%;background:#888;display:flex;align-items:center;justify-content:center}
  .img-crystals{background:radial-gradient(circle at 50% 60%,#cfe6ff 0 14%,rgba(207,230,255,0) 40%),linear-gradient(135deg,#1d2b4a,#3f5f97)}
  .img-books{background:linear-gradient(90deg,#c0392b 0 15%,#2c6fb3 15% 32%,#f2f2f2 32% 48%,#3b8d3e 48% 64%,#e7b530 64% 80%,#7a3d8f 80%)}
  .img-cds{background:radial-gradient(circle at 40% 50%,#dcdcdc 0 20%,#f8f8f8 21% 100%)}
  .img-pendulums{background:radial-gradient(circle at 50% 60%,#d8ecff 0 14%,rgba(216,236,255,0) 40%),linear-gradient(135deg,#16233e,#35538a)}

  /* reiki */
  .reiki{position:absolute;left:128px;top:837px;width:596px;height:190px;
    background:linear-gradient(90deg,var(--pink) 0%,var(--pink-soft) 100%);padding:9px}
  .reiki-text{position:absolute;left:18px;top:16px;width:260px;color:var(--white)}
  .reiki-text h3{font-size:11px;font-weight:600}
  .reiki-text p{margin-top:10px;font-size:7.5px;line-height:1.7}
  .btn-dark{display:inline-block;margin-top:14px;background:#222;color:var(--white);font-size:7px;font-weight:700;padding:6px 10px}
  .reiki-photo{position:absolute;right:9px;top:9px;width:290px;height:172px;
    background:linear-gradient(120deg,#fbeee6 0%,#f1cdb7 45%,#e0a890 70%,#f7f2ee 100%)}

  /* footer */
  .site-footer{position:absolute;left:0;top:1041px;width:851px;height:159px;background:var(--footer)}
  .blog-thumb{position:absolute;left:128px;top:22px;width:60px;height:44px;background:linear-gradient(135deg,#f4d3c4,#c98c7a)}
  .blog-copy{position:absolute;left:198px;top:20px;width:260px;color:#ccc}
  .blog-copy h4{font-size:10px;color:var(--pink);font-weight:600}
  .blog-copy .sub{font-size:8px;color:var(--white);margin-top:1px}
  .blog-copy p{font-size:7px;line-height:1.5;margin-top:3px;color:#aaa}
  .newsletter{position:absolute;left:535px;top:20px;width:190px}
  .newsletter h4{font-size:10px;color:var(--white);font-weight:600}
  .newsletter form{display:flex;margin-top:10px}
  .newsletter .field{width:110px;height:18px;background:var(--white);font-size:7px;color:#999;padding:4px 6px}
  .newsletter .submit{width:36px;height:18px;background:var(--pink);color:var(--white);font-size:7px;text-align:center;padding-top:4px}
  .footer-bottom{position:absolute;left:0;top:100px;width:851px;height:59px;background:var(--footer-deep)}
  .footer-links{position:absolute;left:128px;top:12px;font-size:7.5px;color:#ccc}
  .copyright{position:absolute;left:128px;top:28px;font-size:7px;color:#999}
  .social{position:absolute;left:615px;top:11px;display:flex;gap:5px}
  .social span{width:17px;height:17px;background:var(--pink)}
</style>
</head>
<body>
  <header class="site-header">
    <div class="brand"><span class="brand-dot"></span><span class="brand-name">The Velvet Lantern</span></div>
    <div class="search">Search Products...
      <svg width="10" height="10" viewBox="0 0 10 10"><circle cx="4" cy="4" r="3" fill="none" stroke="#999" stroke-width="1.2"/><line x1="6.2" y1="6.2" x2="9" y2="9" stroke="#999" stroke-width="1.2"/></svg>
    </div>
    <nav class="main-nav">
      <a class="active" href="#">Home</a><a href="#">About</a><a href="#">Online store</a><a href="#">Blog</a><a href="#">Contact us</a>
    </nav>
  </header>

  <section class="hero" role="img" aria-label="Festive gift box with gold ribbon among glittering ornaments">
  </section>
  <div class="hero-caption">Lorem ipsum dolor sit amet, consectetur adipiscing elit, sed diam nonummy nibh euismod tincidunt.</div>
  <div class="slider-dots"><span class="on"></span><span></span><span></span><span></span><span></span></div>

  <section class="welcome">
    <h2 class="section-title">Welcome To The Velvet Lantern</h2>
    <p>Welcome to a gentle space for the curious soul. Browse hand picked crystals, books, music and pendulums chosen with love, and find calm tools that bring light, balance and joy into your everyday life. We hope you leave a little brighter than you came.</p>
  </section>
  <div class="rule" style="top:628px"></div>

  <h2 class="section-title products-title">Our Products</h2>
  <div class="product" style="left:128px"><div class="product-img img-crystals" role="img" aria-label="Sparkling crystals"></div><div class="product-bar">Crystals<i><svg width="6" height="6" viewBox="0 0 6 6"><path d="M2 1l2 2-2 2" fill="none" stroke="#fff" stroke-width="1"/></svg></i></div></div>
  <div class="product" style="left:284px"><div class="product-img img-books" role="img" aria-label="Row of colourful books"></div><div class="product-bar">Books<i><svg width="6" height="6" viewBox="0 0 6 6"><path d="M2 1l2 2-2 2" fill="none" stroke="#fff" stroke-width="1"/></svg></i></div></div>
  <div class="product" style="left:440px"><div class="product-img img-cds" role="img" aria-label="Stack of music CDs"></div><div class="product-bar">CD's<i><svg width="6" height="6" viewBox="0 0 6 6"><path d="M2 1l2 2-2 2" fill="none" stroke="#fff" stroke-width="1"/></svg></i></div></div>
  <div class="product" style="left:596px;width:128px"><div class="product-img img-pendulums" role="img" aria-label="Crystal pendulums"></div><div class="product-bar">Pendulums<i><svg width="6" height="6" viewBox="0 0 6 6"><path d="M2 1l2 2-2 2" fill="none" stroke="#fff" stroke-width="1"/></svg></i></div></div>

  <section class="reiki">
    <div class="reiki-text">
      <h3>We provide Reiki (energy healing)</h3>
      <p>Reiki is a soft, hands on practice that helps the body relax and restore its natural balance. Book a quiet session and let stress melt away as healing energy flows gently through you.</p>
      <span class="btn-dark">LEARN MORE</span>
    </div>
    <div class="reiki-photo" role="img" aria-label="Relaxing Reiki healing session"></div>
  </section>

  <footer class="site-footer">
    <div class="blog-thumb" role="img" aria-label="Blog post thumbnail"></div>
    <div class="blog-copy">
      <h4>From Our Blog</h4>
      <div class="sub">Duis autem vel eum iriure dolor</div>
      <p>Simple crystal rituals to welcome more peace and gentle joy into your home this season.</p>
    </div>
    <div class="newsletter">
      <h4>Newsletter Signup</h4>
      <form><span class="field">Email address</span><span class="submit">Submit</span></form>
    </div>
    <div class="footer-bottom">
      <div class="footer-links">Home &nbsp;|&nbsp; sitemap &nbsp;|&nbsp; privacy &amp; policy &nbsp;|&nbsp; Contact</div>
      <div class="copyright">Copyright © 2014 The Velvet Lantern. All rights reserved.</div>
      <div class="social"><span></span><span></span><span></span><span></span><span></span></div>
    </div>
  </footer>
</body>
</html>
```